Consulting Company PowerPoint Template Design

We are looking for an updated PowerPoint template design or our 55 person energy consulting firm (K7) based in San Francisco (www.kseven-example.com). We would like two versions of the same PowerPoint template in a 16:9 and 4:3 format with our existing logo.

We have an existing color scheme and template and are seeking your help to polish/update the template design for wide format and create a flexible template that is easy to use with content from Excel and Word. Our current template, and a couple of examples that we like are attached.

Specific requests include:

• Dark background for slide title
• A narrow section header
• Maximizing white space for content
• A limited number of well designed Master template layouts to choose from
• A selection of title and section header slides that are not San Francisco specific with some variety to chose from ideally with a focus on energy or nature, graphics/visuals.

For examples of energy specific templates see:
https://www.brightslidehub.example/energy/powerpoint-templates/0.html

Requirements
Must have
• Must use our logo but open to other designs, fonts, and styles for the PowerPoint template.
• Please use our existing color scheme found in the attached Excel file.
• Also we would like the ability to easily copy and paste from our existing/original template to the new template. In other words we would like backward compatibility to apply the new template format to our old PowerPoints that use our existing template.

```html
<!DOCTYPE html>
<html lang="en">
<head>
<meta charset="utf-8">
<title>K7 Presentation Template</title>
<link href="https://fonts.googleapis.com/css2?family=Fira+Sans:wght@300;400;500;600;700&display=swap" rel="stylesheet">
<style>
:root{
  --page:#000000;
  --navy:#0d4a6e;
  --deep:#264766;
  --mid:#3c6590;
  --gold:#d4b06a;
  --teal:#1b5a7c;
  --teal-dark:#144c6b;
  --white:#ffffff;
  --ink:#0d4a6e;
  --grey:#8a8f96;
  --sky:#a9d3ee;
}
*{box-sizing:border-box;margin:0;padding:0}
html,body{width:819px;height:1200px;overflow:hidden;background:var(--page)}
body{position:relative;font-family:"Fira Sans",Arial,sans-serif}
.slide{position:absolute;width:381px;height:286px;overflow:hidden}
.title-slide{background:var(--teal)}
.photo{position:absolute;inset:0}
.photo-solar{background:linear-gradient(135deg,#2c6a8b 0%,#1b5a7c 45%,#174f6e 100%)}
.photo-wind{background:linear-gradient(180deg,#1d5d7f 0%,#1a587a 60%,#155072 100%)}
.photo-plant{background:linear-gradient(180deg,#2a6687 0%,#1f5d7e 50%,#1a5677 100%)}
.photo-pylons{background:linear-gradient(180deg,#1b5a7c 0%,#195678 60%,#134b6a 100%)}
.photo-pylons-b{background:linear-gradient(180deg,#1d5b7d 0%,#185577 60%,#12496a 100%)}
.brand{position:absolute;left:91px;top:133px;display:flex;align-items:center;gap:4px}
.brand-dot{width:38px;height:38px;border-radius:50%;border:1.5px solid var(--white);background:var(--teal-dark)}
.brand-name{color:var(--white);font-weight:500;font-size:15px;letter-spacing:.1px}
.project-title{position:absolute;right:15px;top:199px;font-size:18px;font-weight:500;color:var(--white);letter-spacing:.3px}
.project-title .accent,.slide-header .accent{color:var(--gold)}
.project-sub{position:absolute;right:15px;top:224px;font-size:10px;font-weight:400;color:var(--white);letter-spacing:.2px}
.content-slide{background:var(--white)}
.slide-header{position:absolute;left:0;top:0;width:100%;height:23px;background:var(--navy);color:var(--white);font-size:10px;font-weight:500;padding:5px 6px;letter-spacing:.2px}
.header-rule{position:absolute;left:0;top:23px;width:352px;height:3px;background:var(--gold)}
.header-dot{position:absolute;right:5px;top:11px;width:24px;height:24px;border-radius:50%;background:var(--navy);border:2px solid var(--white);box-shadow:0 0 0 1px var(--navy)}
.slide-footer{position:absolute;left:0;bottom:0;width:100%;height:14px;background:var(--navy);color:var(--white);font-size:8px;font-weight:600;padding:2px 3px}
.page-tab{position:absolute;right:0;bottom:0;width:36px;height:14px;background:var(--gold);clip-path:polygon(5px 0,100% 0,100% 100%,0 100%);color:var(--white);font-size:5.5px;text-align:center;padding-top:4px}
.slide-art{position:absolute;inset:0;width:100%;height:100%}
.bullets{position:absolute;left:14px;top:48px;width:350px;list-style:none}
.bullet{position:relative;padding-left:30px;margin-bottom:18px}
.bullet::before{content:"";position:absolute;left:0;top:1px;width:20px;height:20px;border-radius:50%;background:var(--navy);box-shadow:inset 0 0 0 2px var(--white),0 0 0 1px var(--navy)}
.bullet-title{font-size:9.5px;font-weight:600;color:var(--ink);letter-spacing:.2px;margin-bottom:3px}
.bullet-text{font-size:5.6px;font-weight:300;line-height:1.6;color:var(--grey)}
</style>
</head>
<body>

<!-- Title: solar -->
<section class="slide title-slide" style="left:10px;top:12px">
  <div class="photo photo-solar" role="img" aria-label="Close-up of solar panels under a blue-toned sky"></div>
  <div class="brand"><span class="brand-dot"></span><span class="brand-name">Kestrel Energy Economics</span></div>
  <h1 class="project-title"><span class="accent">PROJECT</span> TITLE HERE</h1>
  <p class="project-sub">Subtext here Subtext here</p>
</section>

<!-- Process diagram -->
<section class="slide content-slide" style="left:418px;top:10px">
  <svg class="slide-art" viewBox="0 0 476 357" aria-hidden="true">
    <path d="M10 232 C40 200 60 160 93 150 C130 140 150 180 193 150 C230 125 260 150 298 150 C340 150 360 185 396 150 C420 128 435 140 455 128" fill="none" stroke="var(--sky)" stroke-width="4"/>
    <path d="M444 118 L462 126 L452 142 Z" fill="var(--sky)"/>
    <g font-family="Fira Sans, Arial, sans-serif" text-anchor="middle">
      <g transform="translate(44,240)"><rect x="-32" y="-32" width="64" height="64" rx="12" transform="rotate(45)" fill="var(--deep)"/><text y="-9" font-size="5" fill="#c7d3df">Duis tortor,</text><text y="-3" font-size="5" fill="#c7d3df">suscipit eget,</text><text y="3" font-size="5" fill="#c7d3df">imperdiet nec,</text><text y="9" font-size="5" fill="#c7d3df">imperdiet</text></g>
      <g transform="translate(143,240)"><rect x="-32" y="-32" width="64" height="64" rx="12" transform="rotate(45)" fill="var(--gold)"/><text y="-9" font-size="5" fill="#5a4a2a">Duis tortor,</text><text y="-3" font-size="5" fill="#5a4a2a">suscipit eget,</text><text y="3" font-size="5" fill="#5a4a2a">imperdiet nec,</text><text y="9" font-size="5" fill="#5a4a2a">imperdiet</text></g>
      <g transform="translate(245,240)"><rect x="-32" y="-32" width="64" height="64" rx="12" transform="rotate(45)" fill="var(--mid)"/><text y="-5" font-size="8" font-weight="600" fill="#fff">Option 03</text><circle cx="1" cy="12" r="4.5" fill="none" stroke="#fff" stroke-width="1.5"/><path d="M-2 15 L-7 20" stroke="#fff" stroke-width="1.8"/></g>
      <g transform="translate(346,240)"><rect x="-32" y="-32" width="64" height="64" rx="12" transform="rotate(45)" fill="var(--deep)"/><text y="-5" font-size="8" font-weight="600" fill="#fff">Option 04</text><ellipse cx="0" cy="8" rx="6" ry="2" fill="#fff"/><rect x="-6" y="10" width="12" height="2" fill="#fff"/><rect x="-6" y="13" width="12" height="2" fill="#fff"/><rect x="-6" y="16" width="12" height="2" fill="#fff"/></g>
      <g transform="translate(93,192)"><rect x="-32" y="-32" width="64" height="64" rx="12" transform="rotate(45)" fill="var(--deep)"/><circle cx="0" cy="-12" r="5" fill="var(--sky)"/><rect x="-2" y="-7" width="4" height="3" fill="var(--sky)"/><text y="11" font-size="8" font-weight="600" fill="var(--sky)">Option 01</text></g>
      <g transform="translate(193,192)"><rect x="-32" y="-32" width="64" height="64" rx="12" transform="rotate(45)" fill="var(--gold)"/><circle cx="0" cy="-10" r="7" fill="var(--deep)"/><text y="-7" font-size="8" font-weight="700" fill="var(--gold)">$</text><text y="11" font-size="8" font-weight="600" fill="var(--deep)">Option 02</text></g>
      <g transform="translate(298,192)"><rect x="-32" y="-32" width="64" height="64" rx="12" transform="rotate(45)" fill="var(--deep)"/><text y="-9" font-size="5" fill="#c7d3df">Duis tortor,</text><text y="-3" font-size="5" fill="#c7d3df">suscipit eget,</text><text y="3" font-size="5" fill="#c7d3df">imperdiet nec,</text><text y="9" font-size="5" fill="#c7d3df">imperdiet</text></g>
      <g transform="translate(396,192)"><rect x="-32" y="-32" width="64" height="64" rx="12" transform="rotate(45)" fill="var(--deep)"/><text y="-9" font-size="5" fill="#c7d3df">Duis tortor,</text><text y="-3" font-size="5" fill="#c7d3df">suscipit eget,</text><text y="3" font-size="5" fill="#c7d3df">imperdiet nec,</text><text y="9" font-size="5" fill="#c7d3df">imperdiet</text></g>
    </g>
  </svg>
  <header class="slide-header"><span class="accent">PROJECT</span> TITLE HERE</header>
  <div class="header-rule"></div>
  <div class="header-dot"></div>
  <footer class="slide-footer">Kestrel Energy Economics<span class="page-tab">01</span></footer>
</section>

<!-- Bullets -->
<section class="slide content-slide" style="left:12px;top:312px">
  <header class="slide-header"><span class="accent">PROJECT</span> TITLE HERE</header>
  <div class="header-rule"></div>
  <div class="header-dot"></div>
  <ul class="bullets">
    <li class="bullet"><h2 class="bullet-title">BULLET TEXT TITLE HERE</h2><p class="bullet-text">There are many variations of passages of Lorem Ipsum available, but the majority have suffered alteration in some form, by injected humour, or randomised words which don't look even slightly believable. It is a long established fact that a reader will be distracted by the readable content of a page when looking at its layout.</p></li>
    <li class="bullet"><h2 class="bullet-title">BULLET TEXT TITLE HERE</h2><p class="bullet-text">There are many variations of passages of Lorem Ipsum available, but the majority have suffered alteration in some form, by injected humour, or randomised words which don't look even slightly believable. It is a long established fact that a reader will be distracted by the readable content of a page when looking at its layout.</p></li>
    <li class="bullet"><h2 class="bullet-title">BULLET TEXT TITLE HERE</h2><p class="bullet-text">There are many variations of passages of Lorem Ipsum available, but the majority have suffered alteration in some form, by injected humour, or randomised words which don't look even slightly believable. It is a long established fact that a reader will be distracted by the readable content of a page when looking at its layout.</p></li>
  </ul>
  <footer class="slide-footer">Kestrel Energy Economics<span class="page-tab">01</span></footer>
</section>

<!-- Focus areas -->
<section class="slide content-slide" style="left:414px;top:311px">
  <svg class="slide-art" viewBox="0 0 476 357" aria-hidden="true" font-family="Fira Sans, Arial, sans-serif">
    <g transform="translate(0,63)">
      <rect x="105" y="0" width="354" height="67" fill="var(--gold)"/>
      <polygon points="10,0 105,0 130,33.5 105,67 10,67" fill="var(--navy)"/>
      <circle cx="64" cy="20" r="6" fill="none" stroke="#fff" stroke-width="1.5"/><path d="M58 30 L70 30 M64 26 L64 34" stroke="#fff" stroke-width="1.5"/>
      <text x="64" y="54" font-size="10" fill="#fff" text-anchor="middle">Focus area</text>
      <text x="143" y="22" font-size="10.5" font-weight="600" fill="#fff">Subtext Title Here</text>
      <text x="143" y="39" font-size="7" font-weight="300" fill="#fff">Brightwell Aid contributes to the eradication of extreme poverty by partnering</text>
      <text x="143" y="51" font-size="7" font-weight="300" fill="#fff">with governments and global agencies to ensure that, through policy</text>
    </g>
    <g transform="translate(0,152)">
      <rect x="105" y="0" width="354" height="67" fill="var(--gold)"/>
      <polygon points="10,0 105,0 130,33.5 105,67 10,67" fill="var(--navy)"/>
      <circle cx="64" cy="18" r="7" fill="none" stroke="#fff" stroke-width="1.5"/><rect x="61" y="25" width="6" height="5" fill="#fff"/>
      <text x="64" y="54" font-size="10" fill="#fff" text-anchor="middle">Focus area</text>
      <text x="143" y="22" font-size="10.5" font-weight="600" fill="#fff">Subtext Title Here</text>
      <text x="143" y="39" font-size="7" font-weight="300" fill="#fff">Brightwell Aid contributes to the eradication of extreme poverty by partnering</text>
      <text x="143" y="51" font-size="7" font-weight="300" fill="#fff">with governments and global agencies to ensure that, through policy</text>
    </g>
    <g transform="translate(0,240)">
      <rect x="105" y="0" width="354" height="67" fill="var(--gold)"/>
      <polygon points="10,0 105,0 130,33.5 105,67 10,67" fill="var(--navy)"/>
      <path d="M55 30 a6 6 0 0 1 2 -11 a8 8 0 0 1 15 2 a5 5 0 0 1 0 9 Z" fill="#fff"/>
      <text x="64" y="54" font-size="10" fill="#fff" text-anchor="middle">Focus area</text>
      <text x="143" y="22" font-size="10.5" font-weight="600" fill="#fff">Subtext Title Here</text>
      <text x="143" y="39" font-size="7" font-weight="300" fill="#fff">Brightwell Aid contributes to the eradication of extreme poverty by partnering</text>
      <text x="143" y="51" font-size="7" font-weight="300" fill="#fff">with governments and global agencies to ensure that, through policy</text>
    </g>
  </svg>
  <header class="slide-header"><span class="accent">PROJECT</span> TITLE HERE</header>
  <div class="header-rule"></div>
  <div class="header-dot"></div>
  <footer class="slide-footer">Kestrel Energy Economics<span class="page-tab">01</span></footer>
</section>

<!-- Title: wind -->
<section class="slide title-slide" style="left:12px;top:609px">
  <div class="photo photo-wind" role="img" aria-label="Wind turbines on a field under a blue-toned sky"></div>
  <div class="brand"><span class="brand-dot"></span><span class="brand-name">Kestrel Energy Economics</span></div>
  <h1 class="project-title"><span class="accent">PROJECT</span> TITLE HERE</h1>
  <p class="project-sub">Subtext here Subtext here</p>
</section>

<!-- Title: power plant -->
<section class="slide title-slide" style="left:410px;top:610px">
  <div class="photo photo-plant" role="img" aria-label="Power plant cooling towers with steam, blue-toned"></div>
  <div class="brand"><span class="brand-dot"></span><span class="brand-name">Kestrel Energy Economics</span></div>
  <h1 class="project-title"><span class="accent">PROJECT</span> TITLE HERE</h1>
  <p class="project-sub">Subtext here Subtext here</p>
</section>

<!-- Title: pylons -->
<section class="slide title-slide" style="left:12px;top:905px">
  <div class="photo photo-pylons" role="img" aria-label="Rows of electricity pylons under a blue-toned sky"></div>
  <div class="brand"><span class="brand-dot"></span><span class="brand-name">Kestrel Energy Economics</span></div>
  <h1 class="project-title"><span class="accent">PROJECT</span> TITLE HERE</h1>
  <p class="project-sub">Subtext here Subtext here</p>
</section>

<!-- Title: single pylon -->
<section class="slide title-slide" style="left:410px;top:905px">
  <div class="photo photo-pylons-b" role="img" aria-label="Transmission tower and power lines, blue-toned"></div>
  <div class="brand"><span class="brand-dot"></span><span class="brand-name">Kestrel Energy Economics</span></div>
  <h1 class="project-title"><span class="accent">PROJECT</span> TITLE HERE</h1>
  <p class="project-sub">Subtext here Subtext here</p>
</section>

</body>
</html>
```